Vitamin B12 Liquid Drops Label

hi, i need a label designed for my vitamin b12 drops that i am going to be selling on shopzello. the label needs to quickly capture the attention of a buyer as he or she is scrolling through the thumbnail search results on shopzello.com my brand is called nralo. i already have an example brand logo i will be using, however, i need help designing the rest of the label. attached are some examples of labels i like for other supplements.some of these examples are pink. i do not want pink. please go for a blue/green color scheme. THE DESIGN MUST BE BOLD

Target Market(s)

adults ages 30 - 64

Font styles to use
Sans Serif

Colors
0455a3
cedeed
3176b5
85acd3
cfdeed
9bcb3b
abd037
cadf82
00a990

Requirements
Must have
• - bold design
• - somewhat gender-neutral color scheme because this will be used equally by men and women
• - B12 MUST be very prominent and visible on the label
Should not have
• - it should not be "crunchy" looking

```html
<!DOCTYPE html>
<html lang="en">
<head>
<meta charset="utf-8">
<title>Nralo Vitamin B12 Label</title>
<link rel="stylesheet" href="https://fonts.googleapis.com/css2?family=Open+Sans:wght@700;800&display=swap">
<style>
  :root {
    --stage: #1e1e1e;
    --label-green: #9bcb3b;
    --label-blue: #0455a3;
    --brand-blue: #0455a3;
    --accent-light: #cadf82;
  }
  html, body {
    margin: 0;
    padding: 0;
    width: 1200px;
    height: 960px;
    overflow: hidden;
    background: var(--stage);
  }
  .label {
    position: absolute;
    left: 210px;
    top: 80px;
    width: 780px;
    height: 800px;
    display: block;
  }
  .label-base { fill: var(--label-blue); }
  .label-top { fill: var(--label-green); }
  .brand-name {
    font-family: "Open Sans", sans-serif;
    font-weight: 800;
    font-size: 180px;
    fill: var(--brand-blue);
  }
  .brand-tagline {
    font-family: "Open Sans", sans-serif;
    font-weight: 700;
    font-size: 30px;
    letter-spacing: 24px;
    fill: var(--label-green);
  }
  .product-name {
    font-family: "Open Sans", sans-serif;
    font-weight: 800;
    font-size: 58px;
    fill: var(--accent-light);
  }
</style>
</head>
<body>
  <svg class="label" viewBox="0 0 780 800" xmlns="http://www.w3.org/2000/svg">
    <rect class="label-base" x="0" y="0" width="780" height="800"/>
    <polygon class="label-top" points="0,0 780,0 609,423 0,423"/>
    <text class="brand-name" x="26" y="401" textLength="554" lengthAdjust="spacingAndGlyphs">NRALO</text>
    <text class="brand-tagline" x="50" y="488">SUPPLEMENTS</text>
    <text class="product-name" x="748" y="758" text-anchor="end" textLength="380" lengthAdjust="spacingAndGlyphs">VITAMIN B12</text>
  </svg>
</body>
</html>
```